Stationary design for boutique production house

We need a stationary design for our production house, 'Lorno Productions' based in Singapore. We produce microfilms as well as podcasts, talkshows and events. Our logo is a stylized icon of our director, who is also the executive producer and host of our programs, Lorno. Our main company colors are Red, Black and white. We would like a clean, minimalist design incorporating our existing company logo that conveys a sense of urbanism and elegance.

Logo and font files are attached. f

Target Market(s)

We focus on lifestyle media rather than entertainment.

Industry/Entity Type

Boutique

Font styles to use
Serif
Sans Serif

Colors
ec1f27
ffffff
000000

Requirements
Must have
• Our company logo and at least one of our company colors.
Nice to have
• Our address and contact information.
Should not have
• Changes made to the company logo (using only certain parts of it is fine though)

```html
<!DOCTYPE html>
<html lang="en">
<head>
<meta charset="utf-8">
<title>Lorno Productions — Business Cards</title>
<link rel="stylesheet" href="https://fonts.googleapis.com/css2?family=Old+Standard+TT:wght@400;700&family=Open+Sans:wght@400&family=Noto+Serif+SC:wght@400&display=swap">
<style>
  :root {
    --red: #ec1f27;
    --white: #ffffff;
    --black: #000000;
    --card: #1d1c1c;
    --text-soft: #d9d9d9;
    --backdrop: #e9e4dc;
  }
  html, body {
    margin: 0;
    padding: 0;
    width: 1200px;
    height: 899px;
    overflow: hidden;
    background: var(--backdrop);
  }
  .stage {
    position: relative;
    width: 1200px;
    height: 899px;
  }
  .card {
    position: absolute;
    top: 152px;
    width: 340px;
    height: 595px;
    background: var(--card);
    box-shadow: 0 10px 24px rgba(0,0,0,0.18);
    color: var(--white);
    font-family: "Old Standard TT", serif;
    text-align: center;
  }
  .card--front { left: 220px; }
  .card--back { left: 640px; }

  .wordmark {
    position: absolute;
    left: 0;
    right: 0;
    display: flex;
    flex-direction: column;
    align-items: center;
  }
  .card--front .wordmark { top: 230px; }
  .card--back .wordmark { top: 64px; }

  .wordmark__dot {
    width: 16px;
    height: 16px;
    border-radius: 50%;
    background: var(--red);
    margin-bottom: 14px;
  }
  .wordmark__name {
    font-family: "Old Standard TT", serif;
    font-weight: 400;
    font-size: 25px;
    line-height: 1.15;
    letter-spacing: 1px;
    color: var(--white);
    text-transform: uppercase;
  }
  .wordmark__tagline {
    display: flex;
    align-items: center;
    gap: 8px;
    margin-top: 8px;
    font-family: "Noto Serif SC", serif;
    font-size: 11px;
    color: var(--text-soft);
  }
  .wordmark__rule {
    width: 44px;
    height: 1px;
    background: var(--text-soft);
  }
  .wordmark__rule--red { background: var(--red); }

  .divider {
    position: absolute;
    left: 50px;
    right: 50px;
    height: 1px;
    background: var(--red);
  }
  .divider--top { top: 248px; }
  .divider--bottom { top: 505px; }

  .person {
    position: absolute;
    top: 266px;
    left: 0;
    right: 0;
  }
  .person__name {
    font-weight: 700;
    font-size: 19px;
    letter-spacing: 1px;
    color: var(--red);
    text-transform: uppercase;
  }
  .person__role {
    margin-top: 4px;
    font-family: "Open Sans", sans-serif;
    font-size: 13px;
    color: var(--white);
  }
  .person__marker {
    display: block;
    margin: 6px auto 0;
  }

  .contact {
    position: absolute;
    top: 352px;
    left: 0;
    right: 0;
    margin: 0;
    padding: 0;
    list-style: none;
    font-size: 13.5px;
    line-height: 22px;
    color: var(--text-soft);
    letter-spacing: 0.4px;
  }
  .contact__web-name { color: var(--red); }
</style>
</head>
<body>
<main class="stage">

  <section class="card card--front" aria-label="Card front">
    <div class="wordmark">
      <span class="wordmark__dot"></span>
      <span class="wordmark__name">Lorno<br>Productions</span>
      <span class="wordmark__tagline">
        <span class="wordmark__rule"></span>洛诺工作室<span class="wordmark__rule wordmark__rule--red"></span>
      </span>
    </div>
  </section>

  <section class="card card--back" aria-label="Card back">
    <div class="wordmark">
      <span class="wordmark__dot"></span>
      <span class="wordmark__name">Lorno<br>Productions</span>
      <span class="wordmark__tagline">
        <span class="wordmark__rule"></span>洛诺工作室<span class="wordmark__rule wordmark__rule--red"></span>
      </span>
    </div>

    <div class="divider divider--top"></div>

    <div class="person">
      <div class="person__name">Lorno Smith</div>
      <div class="person__role">President</div>
      <svg class="person__marker" width="14" height="14" viewBox="0 0 14 14" aria-hidden="true">
        <circle cx="7" cy="7" r="6.5" fill="var(--red)"/>
        <path d="M7 3.2a2.4 2.4 0 0 0-2.4 2.4c0 1.8 2.4 4.6 2.4 4.6s2.4-2.8 2.4-4.6A2.4 2.4 0 0 0 7 3.2z" fill="var(--card)"/>
      </svg>
    </div>

    <ul class="contact">
      <li>Street Address Line 1</li>
      <li>Your City, Postal Code</li>
      <li>T: +00 (0)00 0000</li>
      <li>F: +00 (0)00 0000</li>
      <li>E: info@LornoProductions.com</li>
      <li>www.<span class="contact__web-name">LornoProductions</span>.com</li>
    </ul>

    <div class="divider divider--bottom"></div>
  </section>

</main>
</body>
</html>
```